Liron Vasek Website

Website for my son who is in 7th grade in the US. This will prepare him to show people his accomplishments when applying for a job or going to college. It should have:
* A picture (or multiple pictures)
* A resume page
* A place to share your accomplishments
* Links to his other social profiles
* A contact form

Great to include:
* Internships (show some photos of it along with what you’ve learned).
* Volunteer work.
* A side hustle that you want to highlight

Website sample I like:
https://belinamorud.sitefolio-demo.com/belinamorudtavik

Target Market(s)

For jobs and colleges admissions.

Number of Pages Required

5+ page

Colors

Designer to choose colors to be used in the design.

Requirements
Must have
• * A picture (or multiple pictures)
• * A resume page
• * A place to share your accomplishments
• * Links to his other social profiles
• * A contact form
Nice to have
• Great to include:
• * Internships (show some photos of it along with what you’ve learned).
• * Volunteer work.
• * A side hustle that you want to highlight

```html
<!DOCTYPE html>
<html lang="en">
<head>
<meta charset="utf-8">
<title>Liron Vasek</title>
<link href="https://fonts.googleapis.com/css2?family=Open+Sans:wght@400;600;700&family=Montserrat:wght@500;600;700&display=swap" rel="stylesheet">
<style>
:root{
  --blue:#0a84e0;
  --ink:#333333;
  --text:#555555;
  --muted:#777777;
  --gold:#eeb300;
  --hero-a:#f8c300;
  --hero-b:#f0b400;
  --panel:#f6f8fc;
  --rule:#e4e6ea;
  --white:#ffffff;
  --dark:#333333;
}
*{margin:0;padding:0;box-sizing:border-box}
html,body{width:1200px;height:3920px;overflow:hidden}
body{position:relative;font-family:'Open Sans',sans-serif;color:var(--text);background:var(--white)}
.abs{position:absolute}
section,header,footer{position:absolute;left:0;width:1200px}

/* nav */
.site-nav{top:0;height:72px;background:var(--white)}
.site-nav ul{list-style:none;display:flex;justify-content:center;gap:33px;padding-top:29px;font-family:'Montserrat',sans-serif;font-size:12px;font-weight:600;color:var(--ink)}
.site-nav li.active{color:var(--blue)}

/* hero */
.hero{top:72px;height:567px}
.hero-photo{position:absolute;inset:0;background:linear-gradient(115deg,var(--hero-a) 0%,var(--hero-b) 70%,#e8ac00 100%)}
.hero h1{position:absolute;left:157px;top:130px;font-family:'Montserrat',sans-serif;font-size:56px;font-weight:600;color:var(--white);letter-spacing:-.5px;white-space:nowrap}
.hero p{position:absolute;left:160px;top:214px;width:420px;font-family:'Montserrat',sans-serif;font-size:15.5px;font-weight:500;line-height:24px;color:var(--white)}
.btn-solid{position:absolute;left:160px;top:307px;width:184px;height:44px;background:var(--blue);color:var(--white);font-family:'Montserrat',sans-serif;font-size:11px;font-weight:700;display:flex;align-items:center;justify-content:center}
.arrow{position:absolute;width:22px;height:30px}
.dots{position:absolute;top:496px;left:572px;display:flex;gap:9px}
.dots span{width:9px;height:9px;border-radius:50%;background:var(--ink)}
.dots span:first-child{background:var(--white)}

/* about */
.about{top:639px;height:480px;border-bottom:1px solid var(--rule)}
.about h2{position:absolute;left:143px;top:116px;font-size:32px;font-weight:600;color:var(--ink)}
.about p{position:absolute;left:143px;top:186px;width:362px;font-size:13.5px;line-height:22.5px;color:var(--text)}
.btn-outline{position:absolute;display:flex;align-items:center;justify-content:center;border:2px solid var(--blue);color:var(--ink);font-family:'Montserrat',sans-serif;font-size:11.5px;font-weight:700;background:transparent}
.about .btn-outline{left:143px;top:330px;width:144px;height:42px}
.about-photo{position:absolute;left:604px;top:71px;width:521px;height:336px;background:linear-gradient(160deg,#6b5a4d 0%,#4a3b31 45%,#2c3d55 70%,#3e3028 100%)}

/* resume */
.resume{top:1119px;height:866px}
.section-title{position:absolute;left:0;width:1200px;text-align:center;font-size:32px;font-weight:600;color:var(--ink)}
.resume .section-title{top:50px}
.resume-photo{position:absolute;left:248px;top:139px;width:166px;height:143px;border:2px solid var(--blue);background:linear-gradient(180deg,#6f8a3a,#b08a5a)}
.resume-card{position:absolute;left:414px;top:139px;width:464px;height:143px;background:var(--dark);color:var(--white)}
.resume-card h3{position:absolute;left:86px;top:34px;font-size:29px;font-weight:600}
.resume-card p{position:absolute;left:86px;top:80px;font-size:15px;font-weight:600}
.block-title{position:absolute;font-size:15.5px;color:var(--ink)}
.block-rule{position:absolute;height:3px;background:var(--blue)}
.block-text{position:absolute;font-size:11.5px;line-height:19px;color:var(--muted)}
.checklist{position:absolute;left:308px;top:627px;list-style:none}
.checklist li{display:flex;align-items:center;gap:17px;height:24.2px;font-size:11.5px;color:var(--muted)}
.side-list{position:absolute;list-style:none;font-size:11.5px;line-height:19px;color:var(--muted)}
.resume .btn-outline{left:945px;top:686px;width:182px;height:42px;font-size:11px}

/* achievements */
.achievements{top:1985px;height:543px;background:var(--panel);border-bottom:1px solid var(--rule)}
.achievements .section-title{top:52px}
.card-img{position:absolute;width:240px;height:207px;box-shadow:0 3px 8px rgba(0,0,0,.18)}
.card-cap{position:absolute;width:240px;text-align:center;font-size:15.5px;color:var(--ink)}
.achievements .btn-outline{width:143px;height:43px;font-size:11.5px}

/* internships */
.internships{top:2529px;height:498px}
.internships .section-title{top:54px}
.intern-cap{position:absolute;font-size:15.5px;color:var(--ink)}
.intern-text{position:absolute;font-size:11.5px;line-height:19px;color:var(--muted);width:230px}
.intern-text b{color:var(--ink)}

/* contact */
.contact{top:3027px;height:529px;background:var(--gold)}
.contact h2{position:absolute;left:233px;top:52px;font-size:32px;font-weight:600;color:var(--white)}
.field{position:absolute;left:234px;width:359px;background:var(--white);box-shadow:0 2px 6px rgba(0,0,0,.12);display:flex;align-items:flex-start;gap:8px;padding:11px 0 0 24px;font-size:11.5px;color:var(--ink)}
.field svg{flex:none}
.btn-send{position:absolute;left:354px;top:413px;width:119px;height:38px;border:2px solid var(--white);color:var(--white);font-family:'Montserrat',sans-serif;font-size:11.5px;font-weight:700;display:flex;align-items:center;justify-content:center}
.follow{position:absolute;left:662px;top:180px;width:400px;text-align:center;font-size:35px;line-height:40px;font-weight:600;color:var(--white)}
.social{position:absolute;left:662px;top:295px;width:400px;display:flex;justify-content:center;gap:22px;font-size:15px;font-weight:600;color:var(--white)}
.social span{display:flex;align-items:center;gap:7px}
.social i{width:14px;height:14px;border-radius:50%;background:var(--white);display:block}

/* footer */
.site-footer{top:3556px;height:364px;background:var(--blue);color:var(--white)}
.footer-links{position:absolute;left:281px;top:62px;list-style:none;font-family:'Montserrat',sans-serif;font-size:12px;font-weight:600}
.footer-links li{height:29px}
.contact-item{position:absolute;font-family:'Montserrat',sans-serif;font-size:13px;font-weight:700}
.contact-item .value{display:block;margin-top:12px;font-size:14.5px}
.footer-base{position:absolute;left:0;top:295px;width:1200px;border-top:1px solid rgba(255,255,255,.25);text-align:center;padding-top:22px;font-size:12px}
</style>
</head>
<body>

<header class="site-nav">
  <ul>
    <li class="active">HOME</li><li>PORTFOLIO</li><li>RESUME</li><li>ACHIEVEMENTS</li><li>INTERNSHIPS</li><li>MY VLOUNTEER WORK</li><li>CONTACT</li>
  </ul>
</header>

<section class="hero">
  <div class="hero-photo" role="img" aria-label="Two grey pencils lying on a bright yellow paper background"></div>
  <h1>Hi I'm Liron Vasek</h1>
  <p>Lorem ipsum dolor sit amet, consectetur adipiscing elit, sed do eiusmod tempor incididunt ut labore eta.</p>
  <div class="btn-solid">LEARN MORE ABOUT ME</div>
  <svg class="arrow" style="left:76px;top:233px" viewBox="0 0 22 30"><path d="M16 4 6 15l10 11" fill="none" stroke="#fff" stroke-width="3"/></svg>
  <svg class="arrow" style="left:1101px;top:233px" viewBox="0 0 22 30"><path d="M6 4l10 11-10 11" fill="none" stroke="#fff" stroke-width="3"/></svg>
  <div class="dots"><span></span><span></span><span></span></div>
</section>

<section class="about">
  <h2>About Liron Vasek</h2>
  <p>Lorem ipsum dolor sit amet, consectetur adipiscing elit, sed do eiusmod tempor incididunt ut labore et dolore magna aliqua. Quis ipsum suspendisse ultrices gravida. Risus commodo viverra maecenas accumsan lacus vel facilisis.</p>
  <div class="btn-outline">LEARN MORE</div>
  <div class="about-photo" role="img" aria-label="A child in a blue jacket holding an open map in a brown field"></div>
</section>

<section class="resume">
  <h2 class="section-title">My Resume</h2>
  <div class="resume-photo" role="img" aria-label="Portrait of a young boy crouching on a wooden deck"></div>
  <div class="resume-card"><h3>Liron Vasek</h3><p>Liron Vasek@www.edu</p></div>

  <div class="block-title" style="left:290px;top:325px">Professional info</div>
  <div class="block-rule" style="left:290px;top:355px;width:544px"></div>
  <p class="block-text" style="left:292px;top:367px;width:530px">Lorem ipsum dolor sit amet, consectetur adipiscing elit, sed do eiusmod tempor incididunt ut labore et dolore magna aliqua. Quis ipsum suspendisse ultrices gravida. Risus commodo viverra maecenas accumsan lacus vel facilisis.</p>

  <div class="block-title" style="left:290px;top:436px">Education</div>
  <div class="block-rule" style="left:290px;top:467px;width:544px"></div>
  <p class="block-text" style="left:292px;top:478px;width:530px">Lorem ipsum dolor sit amet, consectetur adipiscing elit, sed do eiusmod tempor incididunt ut labore et dolore magna aliqua. Quis ipsum suspendisse ultrices gravida. Risus commodo viverra maecenas accumsan lacus vel facilisis.</p>

  <div class="block-title" style="left:290px;top:547px">Experience</div>
  <div class="block-rule" style="left:290px;top:577px;width:544px"></div>
  <p class="block-text" style="left:292px;top:589px">Lorem ipsum dolor sit amet, consectetur adipiscing elit,.</p>
  <ul class="checklist">
    <li><svg width="16" height="16" viewBox="0 0 16 16"><circle cx="8" cy="8" r="8" fill="#0a84e0"/><path d="M4.5 8.2l2.3 2.3 4.7-4.8" fill="none" stroke="#fff" stroke-width="1.8"/></svg>Lorem ipsum dolor sit amet, consectetur adipiscing elit,.</li>
    <li><svg width="16" height="16" viewBox="0 0 16 16"><circle cx="8" cy="8" r="8" fill="#0a84e0"/><path d="M4.5 8.2l2.3 2.3 4.7-4.8" fill="none" stroke="#fff" stroke-width="1.8"/></svg>Lorem ipsum dolor sit amet, consectetur adipiscing elit,.</li>
    <li><svg width="16" height="16" viewBox="0 0 16 16"><circle cx="8" cy="8" r="8" fill="#0a84e0"/><path d="M4.5 8.2l2.3 2.3 4.7-4.8" fill="none" stroke="#fff" stroke-width="1.8"/></svg>Lorem ipsum dolor sit amet, consectetur adipiscing elit,.</li>
    <li><svg width="16" height="16" viewBox="0 0 16 16"><circle cx="8" cy="8" r="8" fill="#0a84e0"/><path d="M4.5 8.2l2.3 2.3 4.7-4.8" fill="none" stroke="#fff" stroke-width="1.8"/></svg>Lorem ipsum dolor sit amet, consectetur adipiscing elit,.</li>
    <li><svg width="16" height="16" viewBox="0 0 16 16"><circle cx="8" cy="8" r="8" fill="#0a84e0"/><path d="M4.5 8.2l2.3 2.3 4.7-4.8" fill="none" stroke="#fff" stroke-width="1.8"/></svg>Lorem ipsum dolor sit amet, consectetur adipiscing elit,.</li>
    <li><svg width="16" height="16" viewBox="0 0 16 16"><circle cx="8" cy="8" r="8" fill="#0a84e0"/><path d="M4.5 8.2l2.3 2.3 4.7-4.8" fill="none" stroke="#fff" stroke-width="1.8"/></svg>Lorem ipsum dolor sit amet, consectetur adipiscing elit,.</li>
  </ul>

  <div class="block-title" style="left:948px;top:325px">Courses</div>
  <div class="block-rule" style="left:948px;top:355px;width:176px"></div>
  <ul class="side-list" style="left:948px;top:367px">
    <li>Lorem ipsum dolor sit amet,</li><li>Lorem ipsum dolor sit amet,</li><li>Lorem ipsum dolor sit amet,</li><li>Lorem ipsum dolor sit amet,</li><li>Lorem ipsum dolor sit amet,</li><li>Lorem ipsum dolor sit amet,</li>
  </ul>
  <div class="block-title" style="left:948px;top:492px">Additional Information</div>
  <div class="block-rule" style="left:948px;top:522px;width:176px"></div>
  <ul class="side-list" style="left:948px;top:534px">
    <li>Lorem ipsum dolor sit amet,</li><li>Lorem ipsum dolor sit amet,</li><li>Lorem ipsum dolor sit amet,</li><li>Lorem ipsum dolor sit amet,</li><li>Lorem ipsum dolor sit amet,</li><li>Lorem ipsum dolor sit amet,</li>
  </ul>
  <div class="btn-outline">DOWNLOAD&nbsp; IN PDF FORM</div>
</section>

<section class="achievements">
  <h2 class="section-title">My Achievements</h2>
  <svg class="arrow" style="left:76px;top:289px" viewBox="0 0 22 30"><path d="M16 4 6 15l10 11" fill="none" stroke="#0a84e0" stroke-width="3"/></svg>
  <svg class="arrow" style="left:1101px;top:289px" viewBox="0 0 22 30"><path d="M6 4l10 11-10 11" fill="none" stroke="#0a84e0" stroke-width="3"/></svg>

  <div class="card-img" style="left:145px;top:143px;background:linear-gradient(135deg,#a47a45,#8a6636)" role="img" aria-label="School papers, pencils and a tablet on a brown desk"></div>
  <div class="card-cap" style="left:145px;top:376px">Lorem ipsum dolor sit amet</div>
  <div class="btn-outline" style="left:194px;top:423px">SEE MORE</div>

  <div class="card-img" style="left:482px;top:143px;background:linear-gradient(180deg,#d7dbe2,#9aa3b0 60%,#3c4c6e)" role="img" aria-label="Graduates throwing caps in front of a university building"></div>
  <div class="card-cap" style="left:482px;top:376px">Lorem ipsum dolor sit amet</div>
  <div class="btn-outline" style="left:531px;top:423px">SEE MORE</div>

  <div class="card-img" style="left:817px;top:143px;background:linear-gradient(180deg,#3f3a36,#2b2623 80%,#6c6a68)" role="img" aria-label="Chalkboard covered in math equations"></div>
  <div class="card-cap" style="left:817px;top:376px">Lorem ipsum dolor sit amet</div>
  <div class="btn-outline" style="left:865px;top:423px">SEE MORE</div>
</section>

<section class="internships">
  <h2 class="section-title">Internships</h2>
  <svg class="arrow" style="left:76px;top:219px" viewBox="0 0 22 30"><path d="M16 4 6 15l10 11" fill="none" stroke="#0a84e0" stroke-width="3"/></svg>
  <svg class="arrow" style="left:1101px;top:219px" viewBox="0 0 22 30"><path d="M6 4l10 11-10 11" fill="none" stroke="#0a84e0" stroke-width="3"/></svg>

  <div class="card-img" style="left:145px;top:140px;background:linear-gradient(180deg,#9fb3a8,#6a5a4c 60%,#4a3a30)" role="img" aria-label="Students seated in a classroom with a teacher at the front"></div>
  <div class="intern-cap" style="left:143px;top:375px">Lorem ipsum dolor sit amet</div>
  <p class="intern-text" style="left:145px;top:407px">Lorem ipsum dolor sit amet, consecte-tur adipiscing elit, sed do...<b>Read More</b></p>

  <div class="card-img" style="left:484px;top:140px;background:linear-gradient(120deg,#6a1e24,#9a3038 55%,#d9c7ae)" role="img" aria-label="Student wearing a red backpack"></div>
  <div class="intern-cap" style="left:481px;top:375px">Lorem ipsum dolor sit amet</div>
  <p class="intern-text" style="left:483px;top:407px">Lorem ipsum dolor sit amet, consecte-tur adipiscing elit, sed do...<b>Read More</b></p>

  <div class="card-img" style="left:818px;top:140px;background:linear-gradient(180deg,#d7dbe2,#9aa3b0 60%,#3c4c6e)" role="img" aria-label="Graduates throwing caps in front of a university building"></div>
  <div class="intern-cap" style="left:816px;top:375px">Lorem ipsum dolor sit amet</div>
  <p class="intern-text" style="left:818px;top:407px">Lorem ipsum dolor sit amet, consecte-tur adipiscing elit, sed do...<b>Read More</b></p>
</section>

<section class="contact">
  <h2>Contact Me</h2>
  <div class="field" style="top:132px;height:40px"><svg width="14" height="14" viewBox="0 0 14 14"><circle cx="7" cy="4" r="3.3" fill="#0a84e0"/><path d="M1 14c0-4 2.7-6 6-6s6 2 6 6z" fill="#0a84e0"/></svg>FULL NAME</div>
  <div class="field" style="top:188px;height:40px"><svg width="16" height="12" viewBox="0 0 16 12"><rect x=".5" y=".5" width="15" height="11" fill="#0a84e0"/><path d="M1 1l7 6 7-6" fill="none" stroke="#fff" stroke-width="1.2"/></svg>EMAIL</div>
  <div class="field" style="top:245px;height:39px"><svg width="14" height="14" viewBox="0 0 14 14"><path d="M3 1l2.5 3-1.5 1.5c.8 1.8 2.3 3.3 4 4l1.5-1.5 3 2.5-1.5 2.5C6 12.5 1.5 8 1.5 2.5z" fill="#0a84e0"/></svg>PHONE NUMBER</div>
  <div class="field" style="top:301px;height:79px"><svg width="14" height="13" viewBox="0 0 14 13"><ellipse cx="7" cy="5.5" rx="7" ry="5.5" fill="#0a84e0"/><path d="M2 9l-1 4 4-2.5z" fill="#0a84e0"/></svg>MESSSAGE</div>
  <div class="btn-send">SEND</div>
  <div class="follow">Or Follow Me On<br>Social Media</div>
  <div class="social"><span><i></i>Friendly</span><span><i></i>Pictly</span><span><i></i>Chirpo</span></div>
</section>

<footer class="site-footer">
  <ul class="footer-links">
    <li>HOME</li><li>PORTFOLIO</li><li>RESUME</li><li>ACHIEVEMENTS</li><li>INTERNSHIPS</li><li>MY VLOUNTEER WORK</li><li>CONTACT</li>
  </ul>
  <svg class="abs" style="left:548px;top:63px" width="20" height="22" viewBox="0 0 20 22"><path d="M5 1l3 5-2 2c1.2 3 3.5 5.5 6.5 7l2-2 5 3-2 4C8 20 1 12 1 3z" fill="none" stroke="#fff" stroke-width="1.6"/></svg>
  <div class="contact-item" style="left:573px;top:63px">Call :-<span class="value">555-555-555</span></div>
  <svg class="abs" style="left:815px;top:64px" width="24" height="17" viewBox="0 0 24 17"><rect x="1" y="1" width="22" height="15" fill="none" stroke="#fff" stroke-width="1.6"/><path d="M1 1l11 8 11-8M1 16l8-7M23 16l-8-7" fill="none" stroke="#fff" stroke-width="1.4"/></svg>
  <div class="contact-item" style="left:847px;top:60px">EMAIL :-<span class="value">hello@lironvasek.com</span></div>
  <div class="footer-base">©2019 LironVasek.com. All rights reserved.</div>
</footer>

</body>
</html>
```